Chimney Service company needs new business card design

We need a updated business card with our new logo added. We provide a full range of chimney services throughout Vermont and New Hampshire. The business card will be one sided and color. Attached is our current business card another document showing all the information we would like on the card.
We dont like a lot of flashy colors.... here is a link to our website to get an idea of our branding www.flueguardianvt.example

Target Market(s)

homeowners

Industry/Entity Type

Business

Contact Information for Business Card

See attached sheet for content.

Font styles to use
Serif
Sans Serif

Requirements
Must have
• all information provided on separate sheet
Should not have
• Additional information that may clogg up design

```html
<!DOCTYPE html>
<html lang="en">
<head>
<meta charset="UTF-8">
<title>Flue Guardian – Business Card</title>
<link rel="stylesheet" href="https://fonts.googleapis.com/css2?family=Open+Sans:wght@400;600&family=Archivo:wght@800&display=swap">
<style>
  :root {
    --backdrop: #3b3b3d;
    --card: #1e1e20;
    --card-front: #18181a;
    --emboss: #2e2e31;
    --white: #ffffff;
    --soft: #e6e6e6;
    --red: #c4231f;
    --rule: #8a8a8a;
  }
  * { margin: 0; padding: 0; box-sizing: border-box; }
  html, body { width: 799px; height: 1200px; overflow: hidden; }
  body { background: var(--backdrop); position: relative; font-family: "Open Sans", sans-serif; }

  .card {
    position: absolute; left: 60px; width: 679px; height: 388px;
    border-radius: 3px; box-shadow: 0 10px 30px rgba(0,0,0,.45);
  }
  .card-front { top: 120px; background: var(--card-front); }
  .card-back { top: 692px; background: var(--card); color: var(--white); }

  /* Front */
  .front-lockup { position: absolute; left: 0; right: 0; top: 160px; display: flex; justify-content: center; align-items: center; gap: 16px; }
  .front-dot { width: 18px; height: 18px; border-radius: 50%; background: var(--emboss); }
  .front-name { font-weight: 600; font-size: 40px; color: var(--emboss); letter-spacing: 2px; }

  /* Back */
  .brand { position: absolute; left: 36px; top: 44px; display: flex; align-items: center; gap: 18px; }
  .brand-dot { width: 20px; height: 20px; border-radius: 50%; background: var(--white); }
  .brand-name { font-weight: 600; font-size: 42px; letter-spacing: 2px; line-height: 1; color: var(--white); }

  .services { position: absolute; right: 360px; top: 150px; list-style: none; text-align: right; font-size: 15px; line-height: 23px; color: var(--soft); }
  .services li::after { content: ""; display: inline-block; width: 8px; height: 8px; border-radius: 50%; background: var(--red); margin-left: 9px; vertical-align: 1px; }

  .divider { position: absolute; left: 335px; top: 150px; width: 1px; height: 120px; background: var(--rule); }

  .region { position: absolute; left: 355px; top: 148px; }
  .region-title { font-family: "Archivo", sans-serif; font-weight: 800; font-size: 20px; line-height: 22px; }
  .region-since { margin-top: 6px; width: 240px; border-top: 2px solid var(--red); border-bottom: 2px solid var(--red); text-align: center; font-size: 10px; letter-spacing: 1px; padding: 1px 0; color: var(--soft); }

  .contact { position: absolute; left: 355px; top: 222px; list-style: none; font-size: 14px; line-height: 21px; color: var(--soft); }
  .contact li { display: flex; align-items: center; gap: 10px; }
  .contact svg { width: 12px; height: 12px; fill: var(--red); flex: none; }
  .contact .accent { color: var(--red); }

  .footer-rule { position: absolute; left: 36px; right: 36px; top: 300px; height: 1px; background: var(--rule); }
  .footer { position: absolute; left: 0; right: 0; top: 316px; text-align: center; font-size: 15px; color: var(--soft); word-spacing: 2px; }
  .footer .sep { margin: 0 18px; }
</style>
</head>
<body>

<section class="card card-front" aria-label="Card front">
  <div class="front-lockup">
    <div class="front-dot"></div>
    <div class="front-name">FLUE GUARDIAN</div>
  </div>
</section>

<section class="card card-back" aria-label="Card back">
  <div class="brand">
    <div class="brand-dot"></div>
    <div class="brand-name">FLUE GUARDIAN</div>
  </div>

  <ul class="services">
    <li>Full Masonry Services</li>
    <li>Historic chimney restoration</li>
    <li>Stainless steel liners</li>
    <li>New Chimney installations</li>
    <li>Fully Certified Chimney sweeps</li>
  </ul>

  <div class="divider"></div>

  <div class="region">
    <div class="region-title">SERVING THE NORTH<br>VALLEY REGION</div>
    <div class="region-since">SINCE 1994</div>
  </div>

  <ul class="contact">
    <li>
      <svg viewBox="0 0 24 24" aria-hidden="true"><path d="M6.6 10.8a15.1 15.1 0 0 0 6.6 6.6l2.2-2.2a1 1 0 0 1 1-.25 11.4 11.4 0 0 0 3.6.57 1 1 0 0 1 1 1V20a1 1 0 0 1-1 1A17 17 0 0 1 3 4a1 1 0 0 1 1-1h3.5a1 1 0 0 1 1 1c0 1.25.2 2.45.57 3.57a1 1 0 0 1-.25 1z"/></svg>
      802-555-0147
    </li>
    <li>
      <svg viewBox="0 0 24 24" aria-hidden="true"><path d="M2 5h20v14H2z M2 5l10 8 10-8"/></svg>
      info@flueguardianvt.example
    </li>
    <li>
      <svg viewBox="0 0 24 24" aria-hidden="true"><circle cx="12" cy="12" r="10"/></svg>
      <span>www.<span class="accent">flueguardianvt</span>.example</span>
    </li>
  </ul>

  <div class="footer-rule"></div>
  <p class="footer">Fully Insured - Free Estimates<span class="sep">|</span>Family Owned &amp; Operated</p>
</section>

</body>
</html>
```